Need Web Design for Business Process Outsourcing Company (Quorvane)

Quorvane is a business process outsourcing company. Need a simple site similar to http://www.tallowbrinkhire.com/ but with a more professional and credible look. New to the process; not sure where to start and comparing my options. Please let me know what my options are if I choose to go with you. Logo is attached for your reference. Please use same colorway

Reason: I want the final product to be coded. Please confirm you will be able to code final design.

Industry/Entity Type

Business

Coding

Coded - Design and coding required

```html
<!DOCTYPE html>
<html lang="en">
<head>
<meta charset="utf-8">
<title>Quorvane – Business Process Outsourcing</title>
<link href="https://fonts.googleapis.com/css2?family=Raleway:wght@500;600;700&family=Open+Sans:wght@400;600&display=swap" rel="stylesheet">
<style>
:root{
  --brand:#0a86c4;
  --brand-dark:#0b5d93;
  --nav:#0c5a8e;
  --band:#175e92;
  --ink:#2b2f33;
  --text:#7b7f84;
  --muted:#9a9ea3;
  --line:#e4e6e9;
  --white:#ffffff;
}
*{box-sizing:border-box;margin:0;padding:0}
html,body{width:1200px;height:2663px;overflow:hidden;background:var(--white)}
body{font-family:"Open Sans",Arial,sans-serif;color:var(--text);position:relative}
.section{position:absolute;left:0;width:1200px}
.heading{font-family:"Raleway",Arial,sans-serif;font-weight:700;color:var(--ink);text-align:center;letter-spacing:.5px}
.btn{display:flex;align-items:center;justify-content:center;gap:10px;background:var(--brand);color:var(--white);font-family:"Raleway",Arial,sans-serif;font-weight:600;font-size:15px;border-radius:3px;position:absolute;box-shadow:0 2px 0 var(--brand-dark)}
.btn .caret{width:0;height:0;border-left:5px solid var(--white);border-top:4px solid transparent;border-bottom:4px solid transparent}

/* hero */
.hero{top:0;height:621px;background:linear-gradient(180deg,#5e8c90 0%,#9fb5bb 35%,#b7c3c8 55%,#6f9193 100%)}
.hero::before,.hero::after{content:"";position:absolute;top:0;height:621px}
.hero::before{left:0;width:270px;background:linear-gradient(100deg,#2f5357 0%,#4d7378 70%,rgba(90,130,135,0) 100%)}
.hero::after{right:0;width:300px;background:linear-gradient(260deg,#2c4e52 0%,#4e7479 70%,rgba(90,130,135,0) 100%)}
.brand{position:absolute;left:112px;top:50px;display:flex;align-items:center;gap:12px;z-index:2}
.brand-mark{width:40px;height:40px;background:var(--brand);border-radius:3px}
.brand-name{font-family:"Raleway",Arial,sans-serif;font-weight:700;font-size:34px;color:var(--white)}
.call{position:absolute;right:112px;top:60px;display:flex;align-items:center;gap:10px;color:var(--white);z-index:2}
.call small{display:block;font-size:14px;letter-spacing:1px}
.call strong{display:block;font-family:"Raleway",Arial,sans-serif;font-size:26px;font-weight:600;line-height:1}
.nav{position:absolute;left:112px;top:146px;width:976px;height:62px;background:var(--nav);display:flex;z-index:2}
.nav a{display:flex;align-items:center;justify-content:center;color:var(--white);font-family:"Raleway",Arial,sans-serif;font-weight:700;font-size:12px;text-decoration:none;letter-spacing:.3px;padding:0 38px}
.nav a.active{background:var(--brand);width:124px;padding:0}
.hero-copy{position:absolute;top:342px;left:0;width:1200px;text-align:center;color:var(--white);z-index:2}
.hero-copy h1{font-family:"Raleway",Arial,sans-serif;font-weight:600;font-size:37px;letter-spacing:.5px}
.hero-copy p{width:760px;margin:16px auto 0;font-size:12px;line-height:24px}
.dots{position:absolute;top:576px;left:565px;display:flex;gap:9px;z-index:2}
.dots i{width:9px;height:9px;border-radius:50%;background:rgba(255,255,255,.45)}
.dots i.on{background:var(--brand)}

/* about */
.about{top:621px;height:400px}
.about h2{position:absolute;top:80px;width:100%;font-size:40px}
.about p{position:absolute;top:148px;left:230px;width:740px;text-align:center;font-size:12px;line-height:26px}
.about .btn{left:502px;top:254px;width:194px;height:57px}

/* feature band */
.features{top:1021px;height:358px;background:linear-gradient(90deg,#1b629a 0%,#14578c 33%,#285f8c 50%,#175a8f 66%,#1a5f97 100%);display:flex}
.feature{flex:1;text-align:center;color:var(--white);padding-top:52px;position:relative}
.feature:nth-child(2){background:rgba(255,255,255,.05)}
.feature h3{font-family:"Raleway",Arial,sans-serif;font-weight:600;font-size:20px;margin-top:22px}
.feature p{width:320px;margin:12px auto 0;font-size:12px;line-height:26px;color:#dbe6ef}
.feature .more{display:flex;align-items:center;justify-content:center;gap:8px;margin-top:16px;font-family:"Raleway",Arial,sans-serif;font-weight:600;font-size:14px}
.feature .more .caret{width:0;height:0;border-left:5px solid var(--white);border-top:4px solid transparent;border-bottom:4px solid transparent}

/* news */
.news{top:1379px;height:444px}
.news h2{position:absolute;top:86px;width:100%;font-size:40px}
.post{position:absolute;top:190px;display:flex;gap:25px;width:470px}
.post.one{left:112px}.post.two{left:620px}
.post-media{width:202px;height:146px;flex:none;position:relative}
.post.one .post-media{background:linear-gradient(135deg,#dfe8f0 0%,#b8c6d3 50%,#55708e 100%)}
.post.two .post-media{background:linear-gradient(135deg,#3b6f9c 0%,#2d5f8c 100%);display:flex;flex-direction:column;align-items:center;justify-content:center;color:var(--white);font-family:"Raleway",Arial,sans-serif;font-size:16px;gap:8px}
.post-media .plus{width:12px;height:12px;border-radius:50%;background:var(--white)}
.post h4{font-family:"Raleway",Arial,sans-serif;font-weight:600;font-size:17px;color:var(--ink);margin-top:4px}
.post .date{display:inline-block;background:var(--brand);color:var(--white);font-family:"Raleway",Arial,sans-serif;font-weight:600;font-size:12px;padding:8px 16px;margin-top:14px}
.post p{font-size:11px;line-height:24px;margin-top:6px;width:240px}

/* contact band */
.contact{top:1823px;height:374px;background:linear-gradient(100deg,#ffffff 0%,#f1f2f4 45%,#d9dcdf 75%,#eceef0 100%)}
.contact h2{position:absolute;top:70px;width:100%;font-size:40px}
.contact p{position:absolute;top:145px;left:160px;width:880px;text-align:center;font-size:12px;line-height:26px}
.contact .btn{left:502px;top:241px;width:194px;height:57px}

/* footer */
.footer{top:2197px;height:466px}
.footer h5{font-family:"Raleway",Arial,sans-serif;font-weight:600;font-size:15px;color:var(--ink);position:absolute;top:85px;letter-spacing:.3px}
.quick{left:112px}
.qitem{position:absolute;left:112px;display:flex;gap:18px;align-items:flex-start;font-size:12px;line-height:20px;color:var(--muted)}
.qitem b{display:block;font-weight:400;color:var(--text);font-size:11px}
.links{position:absolute;left:476px;top:142px;list-style:none}
.links li{font-size:12px;color:var(--text);line-height:34px;display:flex;align-items:center;gap:10px}
.links li::before{content:"";width:5px;height:5px;border-right:1.5px solid var(--brand);border-bottom:1.5px solid var(--brand);transform:rotate(-45deg)}
.field{position:absolute;border:1px solid #dcdfe2;font-size:12px;font-style:italic;color:var(--muted);padding:14px 18px}
.submit{position:absolute;left:973px;top:299px;width:112px;height:36px;background:var(--brand);color:var(--white);font-family:"Raleway",Arial,sans-serif;font-weight:700;font-size:11px;display:flex;align-items:center;justify-content:center;gap:8px;border-radius:2px}
.rule{position:absolute;left:112px;top:377px;width:976px;height:1px;background:var(--line)}
.copy{position:absolute;left:112px;top:414px;font-size:11px;color:var(--muted)}
.social{position:absolute;left:988px;top:408px;display:flex;gap:10px}
.social i{width:26px;height:26px;border-radius:50%;background:#e7e9eb}
</style>
</head>
<body>

<header class="section hero" role="img" aria-label="Photo looking up between glass office towers into a pale cloudy sky">
  <div class="brand"><span class="brand-mark"></span><span class="brand-name">Quorvane</span></div>
  <div class="call">
    <svg width="46" height="46" viewBox="0 0 46 46" fill="none" stroke="#fff" stroke-width="3"><circle cx="23" cy="23" r="20"/><ellipse cx="23" cy="23" rx="8" ry="20"/><line x1="3" y1="23" x2="43" y2="23"/></svg>
    <div><small>CALL US</small><strong>555 318 2046</strong></div>
  </div>
  <nav class="nav">
    <a class="active">HOME</a><a>WHO WE ARE</a><a>OUR SOLUTIONS</a><a>OUR EXPERIENCE</a><a>TEAM</a><a>BLOG</a><a>CONTACT US</a>
  </nav>
  <div class="hero-copy">
    <h1>BUSINESS PROCESS OUTSOURCING SOLUTIONS</h1>
    <p>We handle the routine work behind your business so your team can stay focused on growth, clients and the decisions that matter most every day.</p>
  </div>
  <div class="dots"><i></i><i></i><i class="on"></i><i></i></div>
</header>

<section class="section about">
  <h2 class="heading">ABOUT QUORVANE</h2>
  <p>Quorvane supports growing companies with dependable back-office operations, from finance and payroll to customer care and data processing. Our trained specialists follow clear processes, report openly and scale with your needs, so you gain steady quality and lower costs without adding overhead. We treat every account as a long-term partnership built on trust.</p>
  <a class="btn"><span class="caret"></span>LEARN MORE</a>
</section>

<section class="section features" role="img" aria-label="Blue-tinted photo of a business desk with charts behind three service columns">
  <div class="feature">
    <svg width="60" height="56" viewBox="0 0 60 56" fill="#fff"><circle cx="30" cy="14" r="10"/><path d="M12 52c0-12 8-20 18-20s18 8 18 20z"/><circle cx="10" cy="20" r="7"/><path d="M0 46c0-9 4-14 10-14 3 0 5 1 6 2-3 4-5 8-5 12z"/><circle cx="50" cy="20" r="7"/><path d="M60 46c0-9-4-14-10-14-3 0-5 1-6 2 3 4 5 8 5 12z"/></svg>
    <h3>OUR TEAM</h3>
    <p>Skilled people who learn your systems quickly and work as an extension of your own office staff.</p>
    <div class="more"><span class="caret"></span>READ MORE</div>
  </div>
  <div class="feature">
    <svg width="60" height="56" viewBox="0 0 60 56" fill="none" stroke="#fff" stroke-width="5"><circle cx="22" cy="30" r="10"/><g stroke-width="6"><line x1="22" y1="12" x2="22" y2="18"/><line x1="22" y1="42" x2="22" y2="48"/><line x1="4" y1="30" x2="10" y2="30"/><line x1="34" y1="30" x2="40" y2="30"/><line x1="9" y1="17" x2="13" y2="21"/><line x1="31" y1="39" x2="35" y2="43"/><line x1="9" y1="43" x2="13" y2="39"/><line x1="31" y1="21" x2="35" y2="17"/></g><circle cx="46" cy="12" r="6" stroke-width="4"/><circle cx="47" cy="42" r="5" stroke-width="4"/></svg>
    <h3>REINVENTING SERVICES</h3>
    <p>Modern tools and lean methods that make everyday services faster, clearer and easier to measure.</p>
    <div class="more"><span class="caret"></span>READ MORE</div>
  </div>
  <div class="feature">
    <svg width="60" height="56" viewBox="0 0 60 56" fill="none" stroke="#fff" stroke-width="3"><path d="M16 2h20l12 12v40H16z"/><path d="M36 2v12h12"/><line x1="23" y1="26" x2="41" y2="26"/><line x1="23" y1="34" x2="41" y2="34"/><line x1="23" y1="42" x2="41" y2="42"/></svg>
    <h3>SUCCESS STORIES</h3>
    <p>Clients across many sectors who cut costs and improved quality by working alongside us.</p>
    <div class="more"><span class="caret"></span>READ MORE</div>
  </div>
</section>

<section class="section news">
  <h2 class="heading">LATEST NEWS</h2>
  <article class="post one">
    <div class="post-media" role="img" aria-label="Photo of a laptop and pen on a desk with colleagues talking in a bright office"></div>
    <div>
      <h4>Lorem ipsum dolor sit</h4>
      <span class="date">POSTED ON AUG 12, 2016</span>
      <p>Five simple steps to prepare your team for a smooth outsourcing transition this year.</p>
    </div>
  </article>
  <article class="post two">
    <div class="post-media" role="img" aria-label="Blue-tinted photo of a tablet showing charts, with a learn more overlay"><span class="plus"></span>LEARN MORE</div>
    <div>
      <h4>Duis vehicula libero dui</h4>
      <span class="date">POSTED ON AUG 12, 2016</span>
      <p>How shared service centres help small firms reach the standards of larger rivals.</p>
    </div>
  </article>
</section>

<section class="section contact" role="img" aria-label="Faded grey photo of a hand writing with a pen">
  <h2 class="heading">CONTACT QUORVANE</h2>
  <p>Tell us about your current processes and the goals you want to reach. Our advisors will review your needs, answer your questions and outline clear options for working together. Whether you need a single service or a complete support team, we will shape a plan that fits your budget and timeline.</p>
  <a class="btn"><span class="caret"></span>CONTACT NOW</a>
</section>

<footer class="section footer">
  <h5 class="quick">QUICK CONTACT</h5>
  <div class="qitem" style="top:150px">
    <svg width="24" height="38" viewBox="0 0 24 38" fill="none" stroke="#0a86c4" stroke-width="2"><rect x="2" y="1" width="20" height="36" rx="3"/><line x1="2" y1="7" x2="22" y2="7"/><line x1="2" y1="30" x2="22" y2="30"/></svg>
    <div><b>CALL NOW</b>555 318 2046</div>
  </div>
  <div class="qitem" style="top:222px">
    <svg width="38" height="28" viewBox="0 0 38 28" fill="none" stroke="#0a86c4" stroke-width="2"><rect x="1" y="1" width="36" height="26"/><path d="M1 1l18 15L37 1M1 27l13-13M37 27L24 14"/></svg>
    <div><b>OUR MAIL</b>hello@quorvane.com</div>
  </div>
  <div class="qitem" style="top:286px">
    <svg width="38" height="38" viewBox="0 0 38 38" fill="none" stroke="#0a86c4" stroke-width="2"><path d="M19 30C11 20 8 15 8 11a11 11 0 0 1 22 0c0 4-3 9-11 19z"/><circle cx="19" cy="11" r="4"/><path d="M11 26H3l-2 10h36l-2-10h-8"/></svg>
    <div><b>18 Alder Row, Suite 412</b>Harbor City 05</div>
  </div>

  <h5 style="left:476px">QUICK LINKS</h5>
  <ul class="links"><li>About</li><li>Services</li><li>Our Solutions</li><li>News</li><li>Contact Us</li><li>Privacy Policy</li></ul>

  <h5 style="left:715px">SEND A MESSAGE</h5>
  <div class="field" style="left:715px;top:149px;width:176px;height:48px">Name *</div>
  <div class="field" style="left:911px;top:149px;width:176px;height:48px">Email Address *</div>
  <div class="field" style="left:715px;top:215px;width:372px;height:64px">Message *</div>
  <div class="submit">SUBMIT
    <svg width="14" height="8" viewBox="0 0 14 8" fill="none" stroke="#fff" stroke-width="1.6"><line x1="0" y1="4" x2="12" y2="4"/><path d="M9 1l3 3-3 3"/></svg>
  </div>

  <div class="rule"></div>
  <div class="copy">Copyright © 2016 Quorvane. All Right Reserved.</div>
  <div class="social"><i></i><i></i><i></i></div>
</footer>

</body>
</html>
```